Business card design needed

Front of Card:
I would like to have nearly 3/4 of the card from the top in a Pea Green Colour with the word 'Brambleway' written in a(Watermelon Red colour) in the font 'Viner Hand ITC'. Brambleway to be written within the Green colour of the card.

The lower 1/3 of the card I would like to have white with the words:
Home and Garden Styling smaller than the word Brambleway in Black in the font 'Batang', centred underneath the green section.

At the very bottom in one corner in smaller print I would like to have my contact phone number: Pia M:0437619204 and then the email address:
E: brambleaystudio@kelnor.net.au on the other side.

Back of Card:
Back of Card to be White
On one side (Left)
I would like the Heading "Garden" in the same pea green colour as the front and in the Viner Hand ITC font. On the other half of the card I would like 'Home' in the Watermelon Red Colour (same as front colour) and in the font Viner Hand ITC.
Underneath these Headings I would like written in black and in Batang font the following list of services.

Garden Home
Garden Styling Interior Styling
Plant Selection Furniture Selection/Arrangement Garden Maintenance Setting Up Home (after move)
Hedging/Mowing Merchandise and Stylist for
Work w/Local Nurseries Marrow and Finch

Brambleway
Home and Garden Styling
M: 0437619204 E: brambleaystudio@kelnor.net.au

```html
<!DOCTYPE html>
<html lang="en">
<head>
<meta charset="utf-8">
<title>Brambleway – Business Card Concepts</title>
<link rel="stylesheet" href="https://fonts.googleapis.com/css2?family=Caveat:wght@500;600&family=Gowun+Batang&display=swap">
<style>
  :root {
    --pea-green: #1f7a35;
    --watermelon: #e8384f;
    --ink: #2b2b2b;
    --paper: #ffffff;
    --board: #ececec;
    --page: #ffffff;
    --script: "Caveat", cursive;
    --serif: "Gowun Batang", serif;
  }
  * { margin: 0; padding: 0; box-sizing: border-box; }
  html, body {
    width: 1200px; height: 646px; overflow: hidden;
    background: var(--page);
  }
  .canvas { position: relative; width: 1200px; height: 646px; }

  .board {
    position: absolute; top: 0; height: 646px;
    background: var(--board);
  }
  .board--classic { left: 0; width: 570px; }
  .board--banded { left: 631px; width: 569px; }

  .card {
    position: absolute;
    background: var(--paper);
    box-shadow: 0 3px 10px rgba(0,0,0,0.12);
    overflow: hidden;
  }

  /* Front */
  .card__band {
    position: absolute; left: 0; top: 0; width: 100%;
    background: var(--pea-green);
    display: flex; align-items: center; justify-content: center;
  }
  .brand-name {
    font-family: var(--script);
    font-weight: 500;
    font-size: 92px;
    line-height: 1;
    color: var(--watermelon);
    letter-spacing: 1px;
  }
  .tagline {
    position: absolute; left: 0; width: 100%;
    text-align: center;
    font-family: var(--serif);
    font-size: 30px;
    color: var(--ink);
    line-height: 30px;
    white-space: nowrap;
  }
  .contact {
    position: absolute;
    display: flex; align-items: center; gap: 4px;
    font-family: var(--serif);
    font-size: 15px;
    color: var(--ink);
    line-height: 16px;
    white-space: nowrap;
  }
  .contact svg { flex: none; }

  /* Back */
  .service-heading {
    position: absolute;
    font-family: var(--script);
    font-weight: 600;
    font-size: 36px;
    line-height: 1;
  }
  .service-heading--garden { color: var(--pea-green); }
  .service-heading--home { color: var(--watermelon); }

  .service-list {
    position: absolute;
    list-style: none;
    font-family: var(--serif);
    font-size: 13.5px;
    line-height: 20.4px;
    color: var(--ink);
    white-space: nowrap;
  }
  .service-list li { position: relative; padding-left: 10px; }
  .service-list li::before {
    content: ""; position: absolute; left: 0; top: 8px;
    width: 4px; height: 4px; border-radius: 50%;
  }
  .service-list--garden li::before { background: var(--pea-green); }
  .service-list--home li::before { background: var(--watermelon); }

  .stripe { position: absolute; left: 0; display: block; }
</style>
</head>
<body>
<div class="canvas">

  <section class="board board--classic" aria-label="Concept one">
    <article class="card card--front" style="left:42px; top:47px; width:471px; height:262px;">
      <div class="card__band" style="height:170px;">
        <span class="brand-name">Brambleway</span>
      </div>
      <p class="tagline" style="top:177px;">Home and Garden Styling</p>
      <p class="contact" style="left:49px; top:228px;">
        <svg width="12" height="14" viewBox="0 0 12 14" aria-hidden="true"><path d="M3 1 L5 4 L3.8 5.6 C4.6 7.6 5.6 9 7.4 10.2 L8.8 9 L11 11.4 L9.4 13 C5 12.4 1.2 7.4 1 2.4 Z" fill="var(--ink)"/></svg>
        <span>0437619204</span>
      </p>
      <p class="contact" style="left:181px; top:228px;">
        <svg width="18" height="12" viewBox="0 0 18 12" aria-hidden="true"><rect x="1" y="1.5" width="15" height="9" fill="none" stroke="var(--ink)" stroke-width="1"/><path d="M1 1.5 L8.5 7 L16 1.5" fill="none" stroke="var(--ink)" stroke-width="1"/></svg>
        <span>brambleaystudio@kelnor.net.au</span>
      </p>
    </article>

    <article class="card card--back" style="left:41px; top:329px; width:470px; height:260px;">
      <h2 class="service-heading service-heading--garden" style="left:45px; top:30px;">Garden</h2>
      <h2 class="service-heading service-heading--home" style="left:242px; top:30px;">Home</h2>
      <ul class="service-list service-list--garden" style="left:41px; top:98px;">
        <li>Garden Styling</li>
        <li>Plant Selection</li>
        <li>Garden Maintenance</li>
        <li>Hedging/Mowing</li>
        <li>Work w/Local Nurseries</li>
      </ul>
      <ul class="service-list service-list--home" style="left:236px; top:98px;">
        <li>Interior Styling</li>
        <li>Furniture Selection/Arrangement</li>
        <li>Setting Up Home (after move)</li>
        <li>Merchandise and Stylist<br>for Marrow and Finch</li>
      </ul>
      <svg class="stripe" style="top:244px;" width="470" height="16" viewBox="0 0 470 16" aria-hidden="true">
        <rect width="470" height="16" fill="var(--watermelon)"/>
        <polygon points="0,0 270,0 240,16 0,16" fill="var(--pea-green)"/>
      </svg>
    </article>
  </section>

  <section class="board board--banded" aria-label="Concept two">
    <article class="card card--front" style="left:41px; top:49px; width:471px; height:262px;">
      <div class="card__band" style="height:154px;">
        <span class="brand-name">Brambleway</span>
      </div>
      <svg class="stripe" style="top:156px;" width="471" height="16" viewBox="0 0 471 16" aria-hidden="true">
        <rect width="471" height="16" fill="var(--pea-green)"/>
        <polygon points="0,0 245,0 232,16 0,16" fill="var(--watermelon)"/>
      </svg>
      <p class="tagline" style="top:178px;">Home and Garden Styling</p>
      <p class="contact" style="left:48px; top:227px;">
        <svg width="12" height="14" viewBox="0 0 12 14" aria-hidden="true"><path d="M3 1 L5 4 L3.8 5.6 C4.6 7.6 5.6 9 7.4 10.2 L8.8 9 L11 11.4 L9.4 13 C5 12.4 1.2 7.4 1 2.4 Z" fill="var(--ink)"/></svg>
        <span>0437619204</span>
      </p>
      <p class="contact" style="left:180px; top:227px;">
        <svg width="18" height="12" viewBox="0 0 18 12" aria-hidden="true"><rect x="1" y="1.5" width="15" height="9" fill="none" stroke="var(--ink)" stroke-width="1"/><path d="M1 1.5 L8.5 7 L16 1.5" fill="none" stroke="var(--ink)" stroke-width="1"/></svg>
        <span>brambleaystudio@kelnor.net.au</span>
      </p>
    </article>

    <article class="card card--back" style="left:39px; top:329px; width:471px; height:262px;">
      <h2 class="service-heading service-heading--garden" style="left:64px; top:28px;">Garden</h2>
      <h2 class="service-heading service-heading--home" style="left:307px; top:28px;">Home</h2>
      <svg class="stripe" style="top:72px;" width="471" height="16" viewBox="0 0 471 16" aria-hidden="true">
        <rect width="471" height="16" fill="var(--watermelon)"/>
        <polygon points="0,0 256,0 243,16 0,16" fill="var(--pea-green)"/>
      </svg>
      <ul class="service-list service-list--garden" style="left:37px; top:122px;">
        <li>Garden Styling</li>
        <li>Plant Selection</li>
        <li>Garden Maintenance</li>
        <li>Hedging/Mowing</li>
        <li>Work w/Local Nurseries</li>
      </ul>
      <ul class="service-list service-list--home" style="left:238px; top:122px;">
        <li>Interior Styling</li>
        <li>Furniture Selection/Arrangement</li>
        <li>Setting Up Home (after move)</li>
        <li>Merchandise and Stylist<br>for Marrow and Finch</li>
      </ul>
    </article>
  </section>

</div>
</body>
</html>
```